Harlow Creek Church Invite Card

We are a vibrant multigenerational church outside of Raleigh, NC and are wanting a 'church invite card' that we can encourage our members to carry with them so that they can invite their friends to church.

These cards should have a modern feel (see http://brightmosaic.com/neat-card-ideas/ for the feel we are going for), match the branding of our website (www.harlowcreek.org) and include the following information on the back:

Service Times: Sunday @ 8:30 AM and 11:00 AM (Main Focus)
Website: www.harlowcreek.org (Main Focus)
Social Media: (You can simply use the icons for these if desired)
www.facebook.com/harlowcreekchurch
www.instagram.com/harlowcreekchurch
www.youtube.com/harlowcreekyouth
Address: 2847 Tamsin Parkway Alder Ridge, NC 27594 (Not a main focus)
Phone: (919) 482-7093 (Not a main focus)

The front should simply say 'We look forward to meeting you!'

Logos: Attached you will find the necessary logos for this project.

Fonts and Colors: Here are the specific colors (See HCC_Website_Color_Palette.pdf) and fonts that are used on our website.
Pacifico
Helvetica
Open Sans Regular

Target Market(s)

Friends of our congregation

Industry/Entity Type

Church

Contact Information for Business Card

We will likely print through Lantern Printworks. The details of what they need can be found here: http://www.lanternprintworks.com/items/calling-card

Font styles to use
Other font styles liked:
• Pacifico, Helvetica, Open Sans Regular, Bebas Nue

Colors
0592cd
34a7d8
85cae6
cee9f5
0455a3
3176b5
85acd3
cfdfed

Requirements
Must have
• Sleek, eye catching design
Nice to have
• Rounded Corners, Our social media sites (CH, Snap and ClipHarbor)

```html
<!DOCTYPE html>
<html lang="en">
<head>
<meta charset="utf-8">
<title>Harlow Creek Church Invite Card</title>
<link href="https://fonts.googleapis.com/css2?family=Dancing+Script:wght@600&family=Open+Sans:wght@400;600;700&display=swap" rel="stylesheet">
<style>
  :root {
    --stage: #2a2a2c;
    --card: #050505;
    --brand: #1b72c2;
    --white: #ffffff;
    --muted: #9a9a9a;
  }
  * { box-sizing: border-box; margin: 0; padding: 0; }
  html, body { width: 1200px; height: 900px; overflow: hidden; }
  body {
    background: var(--stage);
    font-family: "Open Sans", Helvetica, Arial, sans-serif;
    position: relative;
  }
  .card {
    position: absolute;
    width: 620px;
    height: 354px;
    background: var(--card);
    border-radius: 26px;
    overflow: hidden;
    box-shadow: 0 14px 30px rgba(0,0,0,.45);
  }
  .card-front { left: 90px; top: 70px; }
  .card-back { left: 490px; top: 476px; }

  /* front */
  .greeting-pill {
    position: absolute; left: 50px; top: 124px;
    width: 400px; height: 50px;
    border: 2.5px solid var(--brand); border-radius: 25px;
    display: flex; align-items: center; justify-content: center;
    font-family: "Dancing Script", cursive;
    font-size: 25px; color: var(--white); letter-spacing: .5px;
    white-space: nowrap;
  }
  .front-brand {
    position: absolute; left: 478px; top: 70px; width: 120px;
    font-size: 28px; font-weight: 700; line-height: 1.1;
    color: var(--brand);
  }
  .social-list {
    position: absolute; left: 60px; bottom: 40px;
    display: flex; gap: 22px; list-style: none;
  }
  .social-item {
    display: flex; align-items: center; gap: 8px;
    font-size: 14px; color: var(--white);
  }
  .social-item::before {
    content: ""; width: 22px; height: 22px; border-radius: 4px;
    background: var(--brand);
  }

  /* back */
  .swoosh { position: absolute; left: 0; top: 0; }
  .service-times {
    position: absolute; left: 40px; top: 38px;
    transform: rotate(-6deg); transform-origin: left center;
    font-size: 14px; color: var(--muted); white-space: nowrap;
  }
  .service-times strong { color: var(--brand); font-weight: 700; }
  .back-brand {
    position: absolute; right: 36px; top: 110px;
    font-size: 28px; font-weight: 700; color: var(--white);
    letter-spacing: .5px;
  }
  .rule {
    position: absolute; height: 1.5px; background: var(--white);
  }
  .rule-logo { left: 330px; right: 0; top: 160px; }
  .rule-name { left: 250px; right: 0; top: 246px; }
  .accent-tab {
    position: absolute; left: 0; top: 262px;
    width: 30px; height: 92px;
    background: var(--brand);
    border-radius: 0 18px 0 0;
  }
  .contact { position: absolute; left: 50px; top: 228px; color: var(--white); }
  .contact-name {
    font-size: 22px; font-weight: 700; color: var(--brand);
    letter-spacing: .5px; margin-bottom: 4px;
  }
  .contact-line { font-size: 14px; line-height: 1.35; display: flex; align-items: center; gap: 6px; }
  .contact-line svg { width: 12px; height: 12px; flex: none; }
</style>
</head>
<body>

<section class="card card-front" aria-label="Invite card front">
  <p class="greeting-pill">We look forward to meeting you</p>
  <p class="front-brand">Harlow Creek Church</p>
  <ul class="social-list">
    <li class="social-item">Chatterly</li>
    <li class="social-item">Snapwell</li>
    <li class="social-item">Chirpline</li>
  </ul>
</section>

<section class="card card-back" aria-label="Invite card back">
  <svg class="swoosh" width="620" height="120" viewBox="0 0 620 120">
    <path d="M0,0 H620 V6 Q330,30 0,112 Z" fill="#ffffff"/>
    <path d="M620,6 Q330,30 0,112" fill="none" stroke="#1b72c2" stroke-width="4"/>
  </svg>
  <p class="service-times"><strong>SERVICE TIMES:</strong> Sunday @ <strong>8:30</strong> AM &amp; <strong>11:00</strong> AM</p>

  <p class="back-brand">Harlow Creek Church</p>
  <span class="rule rule-logo"></span>
  <span class="rule rule-name"></span>

  <span class="accent-tab"></span>
  <div class="contact">
    <p class="contact-name">DANIEL REEVES</p>
    <p class="contact-line">2847 Tamsin Parkway</p>
    <p class="contact-line">Alder Ridge, NC 27594</p>
    <p class="contact-line">
      <svg viewBox="0 0 12 12" aria-hidden="true"><path d="M2.5 1 L4.5 1 L5.2 3.6 L4 4.6 Q5 7 7.4 8 L8.4 6.8 L11 7.5 L11 9.5 Q10.5 11 9 11 Q1 10 1 3 Q1 1.5 2.5 1 Z" fill="#1b72c2"/></svg>
      (919) 482-7093
    </p>
    <p class="contact-line">
      <svg viewBox="0 0 12 12" aria-hidden="true"><circle cx="6" cy="6" r="5" fill="none" stroke="#1b72c2" stroke-width="1.3"/><ellipse cx="6" cy="6" rx="2" ry="5" fill="none" stroke="#1b72c2" stroke-width="1"/><path d="M1 6 H11" stroke="#1b72c2" stroke-width="1"/></svg>
      www.harlowcreek.org
    </p>
  </div>
</section>

</body>
</html>
```